I want ideas sample designs for my book cover

Hello,

We need a book cover designed in flat and 3D Versions. We would like to have jpg and png for final output and include a copy of the PSD for future revisions.

Here are the basic details:

Title: The Harvest of Quiet Builders
Author: Norman Quillfeather

Dimensions of book:

Was looking at the Pavo website for dimensions. I thought you may want to go on there and look at the different sizes. I used the 6x9” perfect bound US trade size for my book. You will see that this has a spine width of 0.225”, Cover size of 12.48 x 9.25” and spine begins at 6.125”

If you need background info on the author just to get an idea what he does, please check:

http://NormanQuillfeather.example

IMPORTANT: Please see attached document for a more detailed info:

Exact Title Of book
Back Cover
Spine Info
Measurements of book and dimension
Examples of book covers
Norman's photo attached

Thanks,
Darlene

Industry/Entity Type

Life Coaching

Font styles to use
Serif

Requirements
Must have
• Jpg, png and PSD files
• title
• author
• exact dimensions
• front and back cover
• flat and 3d versions

```html
<!DOCTYPE html>
<html lang="en">
<head>
<meta charset="utf-8">
<title>The Harvest of Quiet Builders — Book Cover</title>
<link rel="stylesheet" href="https://fonts.googleapis.com/css2?family=Playfair+Display:wght@400&family=Questrial&family=Roboto+Condensed:ital,wght@1,500;1,800&family=Archivo:ital,wght@1,900&display=swap">
<style>
  :root {
    --sky-top: #4f8fe0;
    --sky-mid: #7fb2ee;
    --sky-low: #a9cdf3;
    --band-blue: #2a5f9e;
    --sea-deep: #1d4f86;
    --sea-light: #8fbbe3;
    --foot-top: #2b4c7e;
    --foot-bottom: #1b3560;
    --white: #ffffff;
  }
  * { margin: 0; padding: 0; box-sizing: border-box; }
  html, body { width: 801px; height: 1200px; overflow: hidden; background: #ffffff; }
  .cover { position: relative; width: 801px; height: 1200px; overflow: hidden; }

  .sky {
    position: absolute; left: 0; top: 0; width: 801px; height: 342px;
    background: linear-gradient(180deg, var(--sky-top) 0%, var(--sky-mid) 70%, var(--sky-low) 100%);
  }
  .title {
    position: absolute; left: 0; top: 92px; width: 801px;
    font-family: "Playfair Display", "Times New Roman", serif;
    font-weight: 400; font-size: 72px; line-height: 66px;
    color: var(--white); text-align: center; text-transform: uppercase;
    letter-spacing: 1px;
  }

  .tagline-band {
    position: absolute; left: 0; top: 342px; width: 801px; height: 120px;
    background: var(--band-blue);
    display: flex; align-items: center; justify-content: center;
  }
  .tagline {
    font-family: "Questrial", "Century Gothic", sans-serif;
    font-size: 20px; line-height: 27px; color: var(--white); text-align: center;
  }

  .scene {
    position: absolute; left: 0; top: 462px; width: 801px; height: 570px;
    background: linear-gradient(180deg, var(--sky-mid) 0%, #cfe3f6 45%, var(--sea-light) 55%, var(--sea-deep) 78%, #6f9fcd 100%);
  }

  .footer-band {
    position: absolute; left: 0; top: 1032px; width: 801px; height: 168px;
    background: linear-gradient(180deg, var(--foot-top) 0%, var(--foot-bottom) 100%);
    color: var(--white); text-align: center;
  }
  .credit {
    position: absolute; left: 0; top: 22px; width: 801px;
    font-family: "Roboto Condensed", "Arial Narrow", sans-serif;
    font-style: italic; font-weight: 500; font-size: 28px; line-height: 36px;
  }
  .credit strong { font-weight: 800; }
  .author {
    position: absolute; left: 0; top: 74px; width: 801px;
    font-family: "Archivo", "Arial Black", sans-serif;
    font-style: italic; font-weight: 900; font-size: 56px; line-height: 70px;
    letter-spacing: -1px;
  }
</style>
</head>
<body>
<main class="cover">
  <div class="sky" role="img" aria-label="Bright blue sky with soft clouds"></div>
  <h1 class="title">The Harvest of<br>Quiet<br>Builders</h1>

  <section class="tagline-band">
    <p class="tagline">How this ancient wisdom is helping billionaires,<br>industry icons and entrepreneurs to be better leaders,<br>increase impact and leave a legacy.</p>
  </section>

  <div class="scene" role="img" aria-label="Photograph of a man in a dark suit seen from behind, gazing at the sunlit ocean and breaking waves"></div>

  <footer class="footer-band">
    <p class="credit">From the Best Selling Author of <strong>“Stillwater”</strong></p>
    <p class="author">Norman Quillfeather</p>
  </footer>
</main>
</body>
</html>
```